Business Card Design Project - del varosi group

dear Sirs

we need business card design for our group ( DEL Varosi Group ) , i have got the Logo design of our group from pixel harbor in previous , so all need details relating to our group i think available with you, as well as the the chosen logo design

we hope to provide us with business card logo that to be appropaite and satisfactory to us .

thanks

note : logo design of our group is attached .
Updates

Reason: please extend the deadline of my project for additional 15 days because i didn't received appropriate design for our gruop yet . kindly beaware that i have received 77 design till now , supossed to send me 200-250 design at least . thanks

Target Market(s)

contents

name : Kerem EL Nadiri

position : Operation Manager

Industry/Entity Type

Business

Requirements
Must have

• person name

group logo
Nice to have
• logo color matching with back background

```html
<!DOCTYPE html>
<html lang="en">
<head>
<meta charset="utf-8">
<title>DEL Varosi Group – Business Card</title>
<link rel="stylesheet" href="https://fonts.googleapis.com/css2?family=Josefin+Sans:wght@600&family=Open+Sans:wght@400;600;700&display=swap">
<style>
  :root {
    --backdrop: #e9e6e2;
    --card-white: #ffffff;
    --brand-navy: #1b4f93;
    --brand-blue: #1f74c2;
    --text-grey: #555a60;
    --text-white: #ffffff;
  }
  * { box-sizing: border-box; margin: 0; padding: 0; }
  html, body { width: 1200px; height: 758px; overflow: hidden; }
  body {
    background: var(--backdrop);
    font-family: "Open Sans", Arial, sans-serif;
    position: relative;
  }
  .card {
    position: absolute;
    top: 224px;
    width: 540px;
    height: 310px;
    border-radius: 22px;
    overflow: hidden;
    box-shadow: 0 8px 24px rgba(0,0,0,0.18);
  }
  .card--front { left: 40px; background: var(--card-white); }
  .card--back { left: 620px; background: var(--brand-blue); }

  .brand {
    position: absolute;
    display: flex;
    align-items: center;
    gap: 12px;
    font-family: "Josefin Sans", "Century Gothic", sans-serif;
    font-weight: 600;
    letter-spacing: 1px;
    white-space: nowrap;
  }
  .brand__mark { width: 22px; height: 22px; }
  .card--front .brand { left: 40px; top: 46px; font-size: 34px; color: var(--brand-navy); }
  .card--front .brand__mark { background: var(--brand-navy); }
  .card--back .brand { left: 0; right: 0; top: 108px; justify-content: center; font-size: 40px; color: var(--text-white); }
  .card--back .brand__mark { background: var(--text-white); width: 26px; height: 26px; }

  .address {
    position: absolute; left: 40px; top: 132px;
    font-size: 14px; color: var(--text-grey); letter-spacing: 0.3px;
  }
  .contacts {
    position: absolute; left: 40px; top: 168px;
    list-style: none; font-size: 13px; color: var(--text-grey); line-height: 18px;
  }
  .contacts li { display: flex; align-items: center; gap: 6px; }
  .contacts svg { width: 10px; height: 10px; fill: var(--text-grey); }

  .person { position: absolute; right: 36px; top: 140px; text-align: right; }
  .person__name { font-size: 18px; font-weight: 700; color: var(--brand-navy); }
  .person__role { font-size: 13px; color: var(--text-grey); }

  .card__bands { position: absolute; left: 0; bottom: 0; width: 540px; height: 100px; }
  .card__bands path { fill: var(--brand-navy); }

  .web {
    position: absolute; color: var(--text-white); letter-spacing: 1px; font-size: 13px;
  }
  .card--front .web { right: 36px; top: 225px; }
  .card--back .web { left: 0; right: 0; top: 200px; text-align: center; font-size: 18px; letter-spacing: 1.5px; }
</style>
</head>
<body>

<section class="card card--front" aria-label="Business card front">
  <div class="brand"><span class="brand__mark"></span>DEL VAROSI GROUP</div>

  <p class="address">Street name, City, State, zip code</p>

  <ul class="contacts">
    <li><svg viewBox="0 0 10 10"><rect x="2.5" y="0" width="5" height="10" rx="1"/></svg>+2349034417816</li>
    <li><svg viewBox="0 0 10 10"><path d="M2 0h2l1 3-1.5 1a6 6 0 0 0 2.5 2.5L7 5l3 1v2a2 2 0 0 1-2 2A8 8 0 0 1 0 2a2 2 0 0 1 2-2z"/></svg>+2349034417816</li>
    <li><svg viewBox="0 0 10 10"><circle cx="5" cy="3" r="2.5"/><path d="M0 10a5 4 0 0 1 10 0z"/></svg>+2349034417816</li>
    <li><svg viewBox="0 0 10 10"><rect x="0" y="2" width="10" height="7" rx="1"/></svg>name@delvarosigroup.com</li>
  </ul>

  <div class="person">
    <p class="person__name">Kerem EL Nadiri</p>
    <p class="person__role">Operation Manager</p>
  </div>

  <svg class="card__bands" viewBox="0 0 540 100" aria-hidden="true">
    <path d="M300 0H540V40H288L278 56H0V48H284Z"/>
    <path d="M0 66H540V100H0Z"/>
  </svg>
  <p class="web">www.website.com</p>
</section>

<section class="card card--back" aria-label="Business card back">
  <div class="brand"><span class="brand__mark"></span>DEL VAROSI GROUP</div>
  <p class="web">www.website.com</p>
</section>

</body>
</html>
```